NZ First of it's kind solutions directory and marketplace for busy Mums needs a business card design

We need a business card design for our new nationwide business in NZ (long term plans to go global). We provide solutions to the everyday challenges that busy Mums face by connecting them with quality communities and suppliers of carefully selected, relevant products and services. We sell direct via our online marketplace. The final design should communicate our values of inclusivity, quality and smart solutions. Colours should incorporate our logo colour palette of #477077 and #6ba8b2. Our website is at https://www.brightnestmums.example

Target Market(s)

busy Mums, Age 28 – 50, female, income over $100K, location main centres NZ primarily but NZ wide. Is likely juggling work or career with a young family. Probably had hobbies which have fallen by the wayside.
-Wants to succeed in her chosen career without compromising on family life
-to successfully juggle her career without feeling like she is compromising her children
- Is time poor, something always has to give and it’s generally her health (she’ll stay up late, get stressed)
- probably ex corporate or professional career. Has discretional income

Industry/Entity Type

Business

Contact Information for Business Card

Lena Forbisher, Founder, BrightNestMums.example (Strapline Tap; Gather; Sorted), 47 Kowhai Terrace, Ellerslie, Auckland 1051, New Zealand. Mob: 021 483 517 Ph: +64 (0)9 571 4860

Font styles to use
Other font styles liked:
• Raleway, and/or Architects Daughter

Colors
00a990
33b8a4
86cfc6
cfeae6

Requirements
Must have
• the above details, streamline. the logo and colours associated with those logos
Should not have
• foil or metallic colours

```html
<!DOCTYPE html>
<html lang="en">
<head>
<meta charset="utf-8">
<title>BrightNestMums – Business Card</title>
<link rel="stylesheet" href="https://fonts.googleapis.com/css2?family=Questrial&family=Jost:wght@400&display=swap">
<style>
  :root {
    --brand-dark: #477077;
    --brand-card: #537378;
    --brand-light: #6ba8b2;
    --paper: #ffffff;
    --edge: #d4d4d4;
  }
  html, body {
    margin: 0;
    padding: 0;
    width: 1200px;
    height: 1200px;
    overflow: hidden;
    background: var(--paper);
  }
  .canvas {
    position: relative;
    width: 1200px;
    height: 1200px;
  }
  .card {
    position: absolute;
    left: 270px;
    width: 660px;
    height: 427px;
    box-sizing: border-box;
    overflow: hidden;
  }
  .card--front {
    top: 136px;
    background: var(--paper);
    border: 1px solid var(--edge);
  }
  .card--back {
    top: 637px;
    background: var(--brand-card);
  }

  /* Front */
  .brand {
    position: absolute;
    left: 66px;
    top: 160px;
    display: flex;
    align-items: center;
    gap: 22px;
  }
  .brand__dot {
    width: 56px;
    height: 56px;
    border-radius: 50%;
    background: var(--brand-light);
    flex: none;
  }
  .brand__name {
    font-family: "Questrial", sans-serif;
    font-size: 62px;
    line-height: 1;
    color: var(--brand-dark);
    letter-spacing: -0.5px;
  }
  .web {
    position: absolute;
    left: 0;
    right: 0;
    top: 352px;
    text-align: center;
    font-family: "Jost", sans-serif;
    font-size: 19px;
    letter-spacing: 5px;
    color: var(--brand-dark);
  }

  /* Back */
  .back-motif {
    position: absolute;
    left: 0;
    top: 0;
  }
  .contact {
    position: absolute;
    right: 35px;
    top: 72px;
    text-align: right;
    font-family: "Questrial", sans-serif;
    color: var(--paper);
  }
  .contact__name {
    font-size: 36px;
    line-height: 1;
    margin: 0;
    font-weight: 400;
  }
  .contact__role {
    font-size: 25px;
    font-variant: small-caps;
    letter-spacing: 1px;
    margin: 8px 0 0;
  }
  .contact__rule {
    width: 310px;
    height: 3px;
    background: var(--brand-light);
    border: 0;
    margin: 10px 0 0 auto;
  }
  .contact__details {
    margin: 60px 0 0;
    font-size: 21px;
    line-height: 30px;
    font-variant: small-caps;
    letter-spacing: 1.5px;
    font-style: normal;
  }
  .contact__label {
    color: var(--brand-light);
  }
</style>
</head>
<body>
<main class="canvas">

  <section class="card card--front" aria-label="Card front">
    <div class="brand">
      <span class="brand__dot" aria-hidden="true"></span>
      <span class="brand__name">BrightNestMums</span>
    </div>
    <div class="web">WWW.BRIGHTNESTMUMS.EXAMPLE</div>
  </section>

  <section class="card card--back" aria-label="Card back">
    <svg class="back-motif" width="320" height="427" viewBox="0 0 320 427" aria-hidden="true">
      <circle cx="140" cy="239" r="138" fill="var(--brand-light)"/>
    </svg>
    <div class="contact">
      <h1 class="contact__name">Lena Forbisher</h1>
      <p class="contact__role">Founder</p>
      <hr class="contact__rule">
      <address class="contact__details">
        47 Kowhai Terrace,<br>
        Ellerslie, Auckland 1051,<br>
        New Zealand.<br>
        <span class="contact__label">Mob:</span> 021 483 517<br>
        <span class="contact__label">Ph:</span> +64 (0)9 571 4860
      </address>
    </div>
  </section>

</main>
</body>
</html>
```